Mobile app for checking bus arrival

I would like to make the UI much more beautiful and modern. The app is an app to check bus arrival in Singapore.
See here: https://apps.veltrano.com/store/apps/details?id=com.ridoka&hl=en

Based on the question from designers:

1. The first screen shows the favorite bus stop. Each item shows location / street, the top one is the location, second line is the street name. And the number is the bus stop code.

2. Please download the app and try bus stop code with 07589 or 10079, for example. It will bring you to the next screen.

3. The pencil allow you to select color theme, for the list item, and the header.

4. On the second screen, it will show up the list of bus route that available on that bus stop.

5. When you tap on one of them it will show you the 2 subsequent arrival time.

6. Each of the arrival time has the information of availability seats available, seats not available, no more space. (we can use green, yellow, red, respectively).

7. Each of the arrival time has the WAB indicator (Wheelchair availability). Show as icon is preferred.

7. KLT and VOPN are the bus provider in Singapore. 48 means the route /service no.

Requirements:
And check the attachment, see screen 3. I need to add information about the space availability, which has 3 state: seats available, seats not available, no more space. (we can use green, yellow, red, respectively).

Please advise how to show the information.

Target Market(s)

Students, age below 35

Industry/Entity Type

Trivex

Requirements
Must have
• The app currently has the capabilities to select color theme, checkout screen1. It's the button and the list item color.
Nice to have
• Please download the app to see all available colors, and make suggestion to have better color pallete.

```html
<!DOCTYPE html>
<html lang="en">
<head>
<meta charset="utf-8">
<title>Bus Stop 07589</title>
<link rel="stylesheet" href="https://fonts.googleapis.com/css2?family=Roboto:wght@300;400;500;700&display=swap">
<style>
  :root {
    --red: #e2483d;
    --red-light: #e8645a;
    --purple: #9227aa;
    --tile-grey: #d1d1d1;
    --tile-grey-text: #555555;
    --page: #efefef;
    --white: #ffffff;
    --ink: #222222;
    --muted: #777777;
    --dot-grey: #9a9a9a;
    --dot-red: #e0262b;
    --dot-yellow: #f2c400;
    --ad-dark: #3a3630;
    --ad-gold: #d39a2a;
  }
  * { box-sizing: border-box; margin: 0; padding: 0; }
  html, body { width: 676px; height: 1200px; overflow: hidden; }
  body { font-family: "Roboto", Arial, sans-serif; background: var(--page); position: relative; }

  .status-bar { position: absolute; top: 0; left: 0; width: 676px; height: 42px; background: var(--red); color: var(--white); font-size: 23px; }
  .status-bar .carrier { position: absolute; left: 8px; top: 8px; display: flex; align-items: center; gap: 6px; }
  .status-bar .time { position: absolute; left: 0; right: 0; top: 8px; text-align: center; font-weight: 500; }
  .status-bar .power { position: absolute; right: 12px; top: 7px; display: flex; align-items: center; gap: 8px; }

  .app-bar { position: absolute; top: 42px; left: 0; width: 676px; height: 93px; background: var(--red); color: var(--white); }
  .app-bar .back { position: absolute; left: 30px; top: 30px; }
  .app-bar .stop-code { position: absolute; left: 133px; top: 36px; font-size: 37px; font-weight: 400; letter-spacing: 1px; }
  .app-bar .actions { position: absolute; right: 26px; top: 28px; display: flex; gap: 30px; align-items: center; }

  .location-band { position: absolute; top: 135px; left: 0; width: 676px; height: 102px; background: var(--red); color: var(--white); border-top: 1px solid rgba(255,255,255,0.2); }
  .location-band .pin-box { position: absolute; left: 0; top: 0; width: 76px; height: 102px; background: var(--red-light); display: flex; align-items: center; justify-content: center; }
  .location-band .place { position: absolute; left: 76px; right: 0; top: 10px; text-align: center; font-size: 36px; font-weight: 400; }
  .location-band .street { position: absolute; left: 76px; right: 0; top: 57px; text-align: center; font-size: 21px; }

  .tile { position: absolute; width: 321px; display: flex; flex-direction: column; align-items: center; justify-content: center; color: var(--white); box-shadow: 0 1px 2px rgba(0,0,0,0.18); }
  .tile .route { font-size: 76px; font-weight: 500; line-height: 1; }
  .tile .operator { font-size: 28px; font-weight: 500; margin-top: 2px; }
  .tile--red { background: var(--red); }
  .tile--purple { background: var(--purple); }
  .tile--grey { background: var(--tile-grey); color: var(--tile-grey-text); }
  .col-left { left: 12px; }
  .col-right { left: 342px; }
  .row-1 { top: 263px; height: 273px; }
  .row-2 { top: 553px; height: 271px; }
  .row-3 { top: 843px; height: 264px; }

  .tile--open { background: var(--white); justify-content: flex-start; }
  .tile--open .head { width: 100%; height: 112px; background: var(--red); text-align: center; padding-top: 14px; }
  .tile--open .head .route { font-size: 50px; font-weight: 300; }
  .tile--open .head .label { font-size: 18px; font-weight: 500; margin-top: 8px; }
  .arrivals { display: flex; width: 100%; height: 161px; }
  .arrival { flex: 1; position: relative; color: var(--ink); }
  .arrival + .arrival { border-left: 1px solid #e4e4e4; }
  .arrival .caption { position: absolute; left: 12px; top: 12px; font-size: 13px; color: var(--muted); display: flex; align-items: center; gap: 5px; }
  .arrival .eta { position: absolute; left: 10px; top: 52px; font-size: 48px; font-weight: 300; }
  .arrival .eta small { font-size: 21px; font-weight: 400; }
  .arrival .wab { position: absolute; right: 10px; top: 76px; }
  .arrival .load { position: absolute; left: 0; right: 0; top: 112px; border-top: 1px solid #e4e4e4; display: flex; justify-content: center; gap: 14px; padding-top: 18px; }
  .dot { width: 13px; height: 13px; border-radius: 50%; background: var(--dot-grey); }
  .dot--red { background: var(--dot-red); }
  .dot--yellow { background: var(--dot-yellow); }

  .ad-banner { position: absolute; left: 0; top: 1107px; width: 676px; height: 93px; background: #4a4a4a; }
  .ad-banner .art { position: absolute; left: 38px; top: 0; width: 600px; height: 93px; background: linear-gradient(90deg, var(--ad-dark), var(--ad-gold) 50%, #8a6a2c 80%, var(--ad-dark)); }
  .ad-banner .size { position: absolute; left: 62px; top: 8px; font-size: 35px; color: var(--white); line-height: 1.05; }
  .ad-banner .brand { position: absolute; left: 350px; top: 22px; width: 32px; height: 32px; background: var(--white); }
  .ad-banner .brand-name { position: absolute; left: 428px; top: 20px; font-size: 33px; color: var(--white); }
  .ad-banner .info { position: absolute; left: 8px; bottom: 8px; width: 22px; height: 22px; border-radius: 50%; border: 2px solid #bbb; color: #bbb; font-size: 13px; text-align: center; line-height: 18px; }
</style>
</head>
<body>

<div class="status-bar">
  <div class="carrier">
    <svg width="66" height="14" viewBox="0 0 66 14"><g fill="#fff"><circle cx="7" cy="7" r="6"/><circle cx="20" cy="7" r="6"/><circle cx="33" cy="7" r="6"/></g><g fill="none" stroke="#fff" stroke-width="1.5"><circle cx="46" cy="7" r="5.3"/><circle cx="59" cy="7" r="5.3"/></g></svg>
    <span>KORA</span>
    <svg width="22" height="18" viewBox="0 0 22 18"><path d="M11 17 L1 6 A15 15 0 0 1 21 6 Z" fill="#fff"/></svg>
  </div>
  <div class="time">4:21 PM</div>
  <div class="power">
    <svg width="12" height="20" viewBox="0 0 12 20"><path d="M1 5 L11 15 L6 19 V1 L11 5 L1 15" fill="none" stroke="#f0a8a2" stroke-width="1.6"/></svg>
    <span>22%</span>
    <svg width="52" height="24" viewBox="0 0 52 24"><rect x="1" y="1" width="45" height="22" rx="3" fill="none" stroke="#fff" stroke-width="2"/><rect x="4" y="4" width="9" height="16" fill="#fff"/><rect x="47" y="8" width="3" height="8" fill="#fff"/></svg>
  </div>
</div>

<header class="app-bar">
  <svg class="back" width="40" height="34" viewBox="0 0 40 34"><path d="M38 17 H4 M17 3 L3 17 L17 31" fill="none" stroke="#fff" stroke-width="4"/></svg>
  <div class="stop-code">07589</div>
  <div class="actions">
    <svg width="46" height="44" viewBox="0 0 24 23"><path d="M12 1 L15 8.5 L23 9 L17 14 L19 22 L12 17.7 L5 22 L7 14 L1 9 L9 8.5 Z" fill="#fff"/></svg>
    <svg width="40" height="40" viewBox="0 0 40 40"><path d="M9 20 A11 11 0 1 0 14 11" fill="none" stroke="#fff" stroke-width="5"/><path d="M6 4 L17 6 L9 15 Z" fill="#fff"/></svg>
    <svg width="10" height="38" viewBox="0 0 10 38"><g fill="#fff"><circle cx="5" cy="5" r="4.5"/><circle cx="5" cy="19" r="4.5"/><circle cx="5" cy="33" r="4.5"/></g></svg>
  </div>
</header>

<section class="location-band">
  <div class="pin-box">
    <svg width="26" height="34" viewBox="0 0 26 34"><path d="M13 32 C13 32 2 19 2 12 A11 11 0 0 1 24 12 C24 19 13 32 13 32 Z" fill="none" stroke="#fff" stroke-width="2.4"/><circle cx="13" cy="12" r="4" fill="none" stroke="#fff" stroke-width="2.4"/></svg>
  </div>
  <div class="place">Opp calder ctr</div>
  <div class="street">calder rd</div>
</section>

<article class="tile tile--open col-left row-1">
  <div class="head">
    <div class="route">120</div>
    <div class="label">Route No.</div>
  </div>
  <div class="arrivals">
    <div class="arrival">
      <div class="caption"><svg width="15" height="15" viewBox="0 0 16 16"><circle cx="8" cy="8" r="6.8" fill="none" stroke="#777" stroke-width="1.5"/><path d="M8 4 V8 L11 10" fill="none" stroke="#777" stroke-width="1.5"/></svg>Arrival Time</div>
      <div class="eta">7<small>mins</small></div>
      <svg class="wab" width="18" height="18" viewBox="0 0 18 18"><circle cx="4" cy="2.5" r="2" fill="#222"/><path d="M3 5 V10 H9 L12 15" fill="none" stroke="#222" stroke-width="2"/><circle cx="8" cy="12" r="5" fill="none" stroke="#222" stroke-width="2"/></svg>
      <div class="load"><span class="dot"></span><span class="dot dot--red"></span><span class="dot"></span></div>
    </div>
    <div class="arrival">
      <div class="caption"><svg width="15" height="15" viewBox="0 0 16 16"><circle cx="8" cy="8" r="6.8" fill="none" stroke="#777" stroke-width="1.5"/><path d="M8 4 V8 L11 10" fill="none" stroke="#777" stroke-width="1.5"/></svg>Arrival Time</div>
      <div class="eta">21<small>mins</small></div>
      <svg class="wab" width="18" height="18" viewBox="0 0 18 18"><circle cx="4" cy="2.5" r="2" fill="#888"/><path d="M3 5 V10 H9 L12 15" fill="none" stroke="#888" stroke-width="2"/><circle cx="8" cy="12" r="5" fill="none" stroke="#888" stroke-width="2"/></svg>
      <div class="load"><span class="dot"></span><span class="dot"></span><span class="dot dot--yellow"></span></div>
    </div>
  </div>
</article>

<article class="tile tile--red col-right row-1"><div class="route">57</div><div class="operator">KLT</div></article>
<article class="tile tile--red col-left row-2"><div class="route">131</div><div class="operator">KLT</div></article>
<article class="tile tile--grey col-right row-2"><div class="route">851</div><div class="operator">VOPN</div></article>
<article class="tile tile--purple col-left row-3"><div class="route">960</div><div class="operator">VOPN</div></article>
<article class="tile tile--grey col-right row-3"></article>

<aside class="ad-banner">
  <div class="art" role="img" aria-label="Golden ornamental background of a test advertisement banner"></div>
  <div class="size">320x50<br>Test Banner</div>
  <div class="brand"></div>
  <div class="brand-name">AdPlexa by Trivex</div>
  <div class="info">i</div>
</aside>

</body>
</html>
```